We need 3 A2 posters similar look but different enough to be eye catching when changed.

We are a healthcare centre that requires 3 A2 posters - simple, similar but different background colours. These posters will be used within our business to promote services we provide to our clients.

The design should include our logo(attached), a large header and a large section in the middle of the poster to promote the event. We need a blank text box (which WE can insert text to advertise), and 1 image to advertise the event. Please note, we do not need you to choose an image we simply would like you to place a demo to give us an idea of where it should sit.

We want to use the bubble design (attached) as a background and the company colours pink, orange and blue - as on our website. Attached is a copy of our logo and background bubble effect. You can also refer to our website - www.tallowbrookwellness.com.au for more inspiration.

Just to reiterate, these posters should be simple, different but have a uniform feel. They should have an empty middle section that can be edited to add text and a space for an eye catching title and matching image.

Our services include Chiropractic, Podiatry, Nutrition, Massage, Yoga, Pilates and Specialised rehabilitation classes.

Reason: Hi designers, I know we are all busy but I really need more designs from the designers I invited to this project and look forward to receiving more designs. Any questions please let me know. Regards, Marion

Reason: Hi all Increased the budget Regards Marion

Corporate Sydney City office workers

Healthcare

• logo and company colours
section in the middles that can be edited to add text
Space allocated for image placement
Catchy title/header

```html
<!DOCTYPE html>
<html lang="en">
<head>
<meta charset="utf-8">
<title>Tallowbrook Wellness Poster</title>
<link rel="stylesheet" href="https://fonts.googleapis.com/css2?family=Mulish:wght@700;800&display=swap">
<style>
  :root {
    --brand-blue: #5f82f5;
    --text-blue: #5d80ee;
    --sky: #a9c4f3;
    --sky-light: #c3d6f7;
    --brand-orange: #d99140;
    --brand-pink: #c02fe0;
    --white: #ffffff;
    --stage: #f6f6f6;
  }
  * { box-sizing: border-box; margin: 0; padding: 0; }
  html, body {
    width: 943px; height: 1200px; overflow: hidden;
    background: var(--stage);
    font-family: "Mulish", "Century Gothic", sans-serif;
  }
  .poster {
    position: absolute; left: 86px; top: 59px;
    width: 764px; height: 1080px; overflow: hidden;
    background: linear-gradient(160deg, var(--sky-light) 0%, var(--sky) 60%, #9fbcf0 100%);
  }
  .top-band {
    position: absolute; left: 0; top: 0; width: 100%; height: 73px;
    background: var(--brand-blue);
  }
  .brand-name {
    position: absolute; left: 20px; top: 22px;
    display: flex; align-items: center; gap: 10px;
    color: var(--white); font-weight: 800; font-size: 28px; letter-spacing: -0.3px;
  }
  .brand-mark {
    width: 22px; height: 22px; background: var(--brand-orange);
  }
  .header-tab {
    position: absolute; left: 51px; top: 72px; width: 646px; height: 89px;
    background: var(--brand-blue); border-radius: 0 0 12px 12px;
  }
  .header-title {
    position: absolute; right: 18px; top: 30px;
    color: var(--white); font-weight: 700; font-size: 40px; line-height: 1;
  }
  .content-box {
    position: absolute; left: 54px; top: 405px; width: 657px; height: 635px;
    background: var(--white); border: 7px solid var(--brand-blue); border-radius: 18px;
  }
  .photo-slot {
    position: absolute; left: 210px; top: 198px; width: 528px; height: 250px;
    border: 4px solid var(--brand-blue); border-radius: 14px;
    background: linear-gradient(100deg, #8fc3e8 0%, #e8e4df 40%, #cfe4f2 70%, #f2f4f6 100%);
  }
  .intro {
    position: absolute; left: 85px; top: 511px; width: 620px;
    color: var(--text-blue); font-weight: 700; font-size: 21.5px; line-height: 27.8px;
  }
  .intro p + p { margin-top: 27.8px; }
  .footer-bar {
    position: absolute; left: 0; bottom: 0; width: 100%; height: 17px; display: flex;
  }
  .footer-bar .blue { width: 530px; background: var(--brand-blue); }
  .footer-bar .orange { width: 70px; background: var(--brand-orange); }
  .footer-bar .pink { flex: 1; background: var(--brand-pink); }
</style>
</head>
<body>
  <main class="poster">
    <div class="top-band">
      <div class="brand-name"><span>Tallowbrook Wellness</span><span class="brand-mark"></span></div>
    </div>
    <header class="header-tab">
      <h1 class="header-title">Header text space</h1>
    </header>
    <section class="content-box"></section>
    <div class="photo-slot" role="img" aria-label="Photo placeholder: a family preparing fresh vegetables together in a bright kitchen"></div>
    <div class="intro">
      <p>Welcome to Tallowbrook Wellness. Our goal is to<br>achieve the best possible health outcome for our<br>patients. Our unique combination of therapies,<br>structural correction and individualised exercise<br>programs is what sets us apart.</p>
      <p>At anytime, if you have a health condition, even if<br>you feel it is not something we could help you with,<br>contact us and we will find the right solution for you.<br>We are here for the health of our community"</p>
    </div>
    <div class="footer-bar"><span class="blue"></span><span class="orange"></span><span class="pink"></span></div>
  </main>
</body>
</html>
```